Dynamic Business Card for Sports Supplements Company

Hi! I'm looking for an awesome business card to match my existing sports supplement company. I have uploaded my current company logo and screenshot of the front page of my website.

I would like to have something dynamic and interesting and utilize the colors in the website - the reds and purples

The business card should be double sided and focus on a unique eye-catching design on the back and include all the relevant company info.

Most importantly, it should say somewhere: "Sign up on our website for a coupon code."

Target Market(s)

Mostly for women gym goers but it shouldn't be too feminine. It should be in keeping with the website design. It should flow and clearly be connected to it

Industry/Entity Type

Business

Contact Information for Business Card

Lorraine K. Vestal
CEO
LVestal@Quorvanexco.com
www.quorvanexco.com
555.417.3820
P.O. Box 47315
Alderfield, Westmont 00000

Sign up on our website for a coupon code

Font styles to use
Serif
Sans Serif
Other font styles liked:
• Novecento font family and "Quorvanex" is in AR Destine font

Requirements
Must have
• One side should be a bold Quorvanex logo design. Even just the symbol itself may be o.k. (see attached file)

```html
<!DOCTYPE html>
<html lang="en">
<head>
<meta charset="utf-8">
<title>Quorvanex Business Card</title>
<link href="https://fonts.googleapis.com/css2?family=Work+Sans:wght@400;500;600;700&display=swap" rel="stylesheet">
<style>
  :root{
    --bg:#c8c8c8;
    --red:#e32226;
    --ink:#4a4a4a;
    --dark:#1e1e1e;
    --white:#ffffff;
  }
  *{margin:0;padding:0;box-sizing:border-box}
  html,body{width:1200px;height:1000px;overflow:hidden;background:var(--bg);font-family:"Work Sans",sans-serif}
  .sheet{position:relative;width:1200px;height:1000px}
  .card{position:absolute;top:346px;width:540px;height:308px;box-shadow:0 6px 18px rgba(0,0,0,.25);overflow:hidden}
  .card--front{left:45px;background:var(--white)}
  .card--back{left:615px;background:var(--dark);display:flex;flex-direction:column;align-items:center;justify-content:center}

  .brand{position:absolute;left:44px;top:28px}
  .brand__name{font-weight:700;font-size:24px;letter-spacing:1px;color:var(--red);text-transform:uppercase;line-height:1}
  .brand__tag{font-size:10px;color:var(--red);letter-spacing:.6px;margin-top:3px}

  .person{position:absolute;left:44px;top:102px}
  .person__name{font-size:20px;font-weight:700;color:var(--ink);text-transform:uppercase;letter-spacing:.5px;line-height:1}
  .person__name span{color:var(--red)}
  .person__role{font-size:11px;font-weight:700;color:var(--ink);margin-top:4px}

  .contacts{position:absolute;left:44px;top:150px;list-style:none}
  .contacts li{display:flex;align-items:center;gap:8px;font-size:13px;color:var(--ink);height:19px}
  .contacts svg{width:12px;height:12px;flex:none}
  .contacts .accent{color:var(--red)}
  .address{position:absolute;left:44px;top:214px;font-size:13px;color:var(--ink);line-height:1.3}

  .feature-block{position:absolute;right:56px;top:104px;width:128px;height:128px;background:var(--red)}

  .promo{position:absolute;left:0;bottom:0;width:100%;height:38px;background:var(--red);display:flex;align-items:center;justify-content:center}
  .promo__mark{position:absolute;left:20px;width:14px;height:14px;background:var(--white)}
  .promo__text{color:var(--white);font-size:12.5px;font-weight:500;letter-spacing:1.2px;text-transform:uppercase}

  .back__square{width:40px;height:40px;background:var(--red);margin-bottom:14px}
  .back__name{font-size:30px;font-weight:700;letter-spacing:1.5px;color:var(--white);text-transform:uppercase;line-height:1}
  .back__tag{font-size:11px;color:var(--white);letter-spacing:.8px;margin-top:5px}
</style>
</head>
<body>
<main class="sheet">
  <section class="card card--front" aria-label="Card front">
    <div class="brand">
      <div class="brand__name">Quorvanex</div>
      <div class="brand__tag">your training ally</div>
    </div>

    <div class="person">
      <div class="person__name">Lorraine <span>K. Vestal</span></div>
      <div class="person__role">CEO</div>
    </div>

    <ul class="contacts">
      <li>
        <svg viewBox="0 0 12 12" aria-hidden="true"><path fill="#e32226" d="M2 1h2.5l1 3-1.5 1a6 6 0 0 0 3 3l1-1.5 3 1V11c-5 0-9-4-9-9z"/></svg>
        555.417.3820
      </li>
      <li>
        <svg viewBox="0 0 12 12" aria-hidden="true"><rect x="0.5" y="2" width="11" height="8" fill="#e32226"/><path d="M1 2.5l5 4 5-4" stroke="#fff" stroke-width="1" fill="none"/></svg>
        LVestal@Quorvanexco.com
      </li>
      <li>
        <svg viewBox="0 0 12 12" aria-hidden="true"><circle cx="7" cy="5" r="3.5" stroke="#e32226" stroke-width="1.5" fill="none"/><path d="M4.5 7.5L1 11" stroke="#e32226" stroke-width="2"/></svg>
        <span>www.<span class="accent">quorvanexco</span>.com</span>
      </li>
    </ul>

    <p class="address">P.O. Box 47315 Alderfield,<br>Westmont 00000</p>

    <div class="feature-block" aria-hidden="true"></div>

    <div class="promo">
      <span class="promo__mark" aria-hidden="true"></span>
      <span class="promo__text">Sign up on our website for a coupon code</span>
    </div>
  </section>

  <section class="card card--back" aria-label="Card back">
    <div class="back__square" aria-hidden="true"></div>
    <div class="back__name">Quorvanex</div>
    <div class="back__tag">your training ally</div>
  </section>
</main>
</body>
</html>
```